Menu Redesign - Upscale Restaurant

We are looking to have our lunch and dinner menus redesigned. We are looking to elevate the signs some, no emojis. We want a clean but elevated look, please refer to Marlowe’s Dining Collective food menu and Vesper Tavola’s beverage menu. The company we’ve been using presented us with the attached menu / it’s filled with spelling and grammar errors.

Industry/Entity Type

Restaurant - Hospitality

```html
<!DOCTYPE html>
<html lang="en">
<head>
<meta charset="utf-8">
<title>Miss Delphine’s Creole House – Menu</title>
<link rel="stylesheet" href="https://fonts.googleapis.com/css2?family=Poppins:wght@400;500;600;700&display=swap">
<style>
:root{
  --red:#C8202F;
  --sand:#E6D2B9;
  --cream:#F4EFE7;
  --ink:#262626;
  --rule:#8a8178;
  --backdrop:#FFFFFF;
}
*{margin:0;padding:0;box-sizing:border-box}
html,body{width:1200px;height:927px;overflow:hidden;background:var(--backdrop)}
body{position:relative;font-family:"Poppins",sans-serif;color:var(--ink);font-size:8.1px;line-height:11px}
.page{position:absolute;top:108px;width:503px;height:711px;overflow:hidden;background:var(--cream)}
.page--food{left:46px}
.page--drinks{left:651px}
.page__bg{position:absolute;inset:0;width:100%;height:100%}
.brand{position:absolute;color:var(--red);font-weight:500;text-transform:uppercase;letter-spacing:1px}
.brand__name{display:block;line-height:1}
.brand__sub{display:block;text-align:right;letter-spacing:.5px}
.page--food .brand{left:22px;top:18px}
.page--food .brand__name{font-size:27px}
.page--food .brand__sub{font-size:12px;margin-top:16px}
.page--drinks .brand{left:27px;top:16px}
.page--drinks .brand__name{font-size:17px}
.page--drinks .brand__sub{font-size:7.5px;margin-top:6px;font-weight:600}
.heading{color:var(--red);font-weight:700;font-size:14.5px;line-height:15px;text-transform:uppercase;text-align:center}
.note{font-style:italic;font-size:6.2px;line-height:8px}
.hours{position:absolute;left:274px;top:26px}
.hours .heading{text-align:left;font-size:13.5px}
.hours p{font-size:7.8px;line-height:11px}
.col{position:absolute}
.divider{position:absolute;border-left:1px dashed var(--rule)}
.item{margin-bottom:4px}
.item h4{display:flex;justify-content:space-between;font-weight:600;font-size:8.1px;line-height:11px;margin-bottom:4px}
.item h4 span:last-child{color:var(--red);font-weight:700;font-size:9.2px;white-space:nowrap;padding-left:6px}
.item h4 em{display:block;font-style:italic;font-weight:400;font-size:5.5px;line-height:6px;text-align:right}
.item--tight h4{margin-bottom:0}
.policies{position:absolute;left:251px;top:626px;width:240px}
.policies .heading{text-align:left}
.policies p{margin-top:6px}
.site{position:absolute;left:16px;top:676px;font-size:9.4px;display:flex;align-items:center;gap:5px}
.site i{width:9px;height:9px;border-radius:50%;background:var(--red);display:inline-block}
.sides{list-style:none}
.sides li{display:flex;justify-content:space-between;font-weight:600;line-height:10.8px}
.sides li span:last-child{color:var(--red);font-weight:700}
.bev-price{color:var(--red);font-weight:700}
.bev-row{display:flex;justify-content:space-between}
</style>
</head>
<body>

<section class="page page--food" aria-label="Food menu">
  <svg class="page__bg" viewBox="0 0 503 711" preserveAspectRatio="none" aria-hidden="true">
    <rect width="503" height="711" fill="var(--cream)"/>
    <path d="M0 0H503V213C470 300 400 370 290 405C200 432 90 420 0 372Z" fill="var(--sand)"/>
  </svg>

  <div class="brand"><span class="brand__name">Miss Delphine’s</span><span class="brand__sub">Creole House</span></div>

  <div class="hours">
    <h2 class="heading">Happy Hour Food &amp; Drinks</h2>
    <p style="margin-top:4px">Monday to Friday 3:00PM - 6:00PM</p>
    <p>Bar Seats and high top tables by bar ONLY</p>
    <h2 class="heading" style="margin-top:5px">Brunch</h2>
    <p style="margin-top:5px">Saturday &amp; Sunday 11:00AM - 3:30PM</p>
  </div>

  <div class="col" style="left:16px;top:118px;width:150px">
    <h2 class="heading">Starters</h2>
    <p class="note" style="margin:1px 0 5px">All served with Cajun fries unless noted.</p>
    <div class="item"><h4><span>Seafood Basket</span><span>$18</span></h4><p>Choice of fresh battered catfish or golden fried shrimp served with seasoned fries.</p></div>
    <div class="item"><h4><span>New Orleans Shrimp</span><span>$16</span></h4><p>Creamy garlic Cajun sautéed shrimp served with toasted bread.</p></div>
    <div class="item"><h4><span>Voodoo Shrimp</span><span>$16</span></h4><p>Crispy fried shrimp tossed in house-made Voodoo sauce, topped with fresh jalapeños and blue cheese crumbles.</p></div>
    <div class="item"><h4><span>Cup of Gumbo</span><span>$15</span></h4><p>Slow-cooked Cajun broth with andouille sausage, shrimp, and chicken, topped with rice.</p></div>
    <div class="item"><h4><span>Raw Oysters</span><span>$16</span></h4><p>Freshly shucked Blue Point oysters served over ice with lemon, horseradish, hot sauce, and mignonette.</p></div>
    <div class="item"><h4><span>Chargrilled Oysters</span><span>$17</span></h4><p>Blue Point oysters grilled with Cajun garlic butter and a four-cheese blend.</p></div>
    <div class="item"><h4><span>Oysters Rockefeller</span><span>$18</span></h4><p>Blue Point oysters topped with creamy spinach and cheese.</p></div>
    <div class="item"><h4><span>Jambalaya Oysters</span><span>$22</span></h4><p>Blue Point oysters topped with creamy Cajun shrimp and crab.</p></div>
    <div class="item"><h4><span>Make It a Platter</span><span>$30<em>(Serves 3)</em></span></h4><p>Choose any three starters. Seafood starters added to the platter are an upcharge.</p></div>
  </div>

  <div class="divider" style="left:171px;top:147px;height:461px"></div>

  <div class="col" style="left:180px;top:117px;width:150px">
    <h2 class="heading" style="margin-bottom:11px">Small Plates</h2>
    <div class="item"><h4><span>Creole Wings</span><span>$16</span></h4><p>Crispy bone-in wings tossed in your choice of:<br>Plain • Mambo • Voodoo • Hot honey lemon pepper</p></div>
    <div class="item"><h4><span>Spinach Dip</span><span>$13</span></h4><p>Chopped spinach in a four-cheese blend with tortilla chips. Add jumbo lump crab +$6</p></div>
    <div class="item"><h4><span>Fried Green Tomatoes</span><span>$13</span></h4><p>Panko-crusted green tomatoes. Add jumbo lump crab +$6</p></div>
    <div class="item"><h4><span>Seafood Rolls</span><span>$18</span></h4><p>Shrimp, crab, and cheese in a crispy egg roll. Served with remoulade.</p></div>
    <div class="item"><h4><span>Steak &amp; Cheese Rolls</span><span>$16</span></h4><p>Philly steak, onions, peppers, and cheese in an egg roll with chipotle mayo.</p></div>
    <div class="item"><h4><span>Bayou Rolls</span><span>$15</span></h4><p>Chicken, peppers, and cheese in a crispy roll with remoulade.</p></div>
    <div class="item"><h4><span>Fried Deviled Eggs</span><span>$13</span></h4><p>Whipped seasoned eggs with sweet relish.<br>Add shrimp or jumbo lump crab (upcharge)</p></div>
    <div class="item"><h4><span>Hot Honey Salmon Bites</span><span>$15</span></h4><p>Fried salmon bites tossed in hot honey.</p></div>
    <div class="item"><h4><span>Stuffed Shrimp</span><span>$18</span></h4><p>Shrimp stuffed with crabmeat, fried golden, served over jalapeño corn succotash.</p></div>
  </div>

  <div class="divider" style="left:335px;top:147px;height:461px"></div>

  <div class="col" style="left:344px;top:116px;width:147px">
    <h2 class="heading" style="margin-bottom:12px">Salad</h2>
    <div class="item"><h4><span>Caesar</span><span>$12</span></h4><p>Romaine, parmesan-romano, croutons, house Caesar dressing.</p></div>
    <div class="item"><h4><span>Crispy Chicken House</span><span>$17</span></h4><p>Field greens, dried cranberries, tomatoes, cucumbers, boiled egg, cheddar, croutons, fried chicken breast, Champagne vinaigrette.</p></div>
    <div class="item"><h4><span>Honey Caribbean Salmon</span><span>$22</span></h4><p>Field greens, corn, tomatoes, cucumber, red onion, buttermilk herb dressing.</p></div>
    <div class="item"><h4><span>Grilled Pear &amp; Walnut</span><span>$19</span></h4><p>Greens, charred pear, cucumber, red onion, tomatoes, dried cranberries, walnuts, blackened chicken.</p></div>
    <h2 class="heading" style="margin-top:16px">Sandwiches</h2>
    <p class="note" style="margin:0 0 6px">Served with fries.</p>
    <div class="item"><h4><span>Loaded Burger</span><span>$18</span></h4><p>Beef patty, white cheddar, lettuce, tomato, fried egg, mambo sauce.</p></div>
    <div class="item"><h4><span>Miss Delphine’s Chicken Sandwich</span><span>$18</span></h4><p>Crispy fried chicken dipped in honey garlic sauce, white cheddar, lettuce, tomato, pickle.</p></div>
    <div class="item"><h4><span>Crabcake Sandwich</span><span>$25</span></h4><p>Jumbo lump crab cake (fried or pan-seared), lettuce, tomato, bacon, remoulade.</p></div>
  </div>

  <div class="policies">
    <h2 class="heading">House Policies</h2>
    <p>Please read menu descriptions carefully before ordering.<br>A 20% gratuity is automatically added to all checks.<br>Parties of 4 or more will be placed on one check.</p>
  </div>

  <div class="site"><i></i>www.missdelphines.example</div>
</section>

<section class="page page--drinks" aria-label="Entrées and beverages menu">
  <svg class="page__bg" viewBox="0 0 503 711" preserveAspectRatio="none" aria-hidden="true">
    <rect width="503" height="711" fill="var(--cream)"/>
    <path d="M0 0H503V213C470 300 400 365 300 390C200 412 90 405 0 377Z" fill="var(--sand)"/>
  </svg>

  <div class="brand"><span class="brand__name">Miss Delphine’s</span><span class="brand__sub">Creole House</span></div>

  <div class="col" style="left:16px;top:61px;width:150px">
    <h2 class="heading" style="margin-left:60px;margin-bottom:13px">Entrées</h2>
    <div class="item"><h4><span>Miss Delphine’s Fried Chicken</span><span>$23</span></h4><p>Half chicken seasoned and fried golden. Served with two sides.</p></div>
    <div class="item"><h4><span>Fried Catfish</span><span>$25</span></h4><p>Catfish fried golden or blackened. Served with two sides.</p></div>
    <div class="item"><h4><span>Loaded Creole Pasta</span><span>$50</span></h4><p>Shrimp, crabmeat, and crab leg over creamy Cajun linguine.</p></div>
    <div class="item"><h4><span>Jambalaya Pasta</span><span>$27</span></h4><p>Shrimp, chicken, andouille sausage, and vegetables in Cajun cream sauce.<br>Rice option available.</p></div>
    <div class="item"><h4><span>Gumbo with Cornbread</span><span>$25</span></h4><p>Roux-based gumbo with chicken, vegetables, sausage, shrimp, and scallion rice.<br>Add crab leg +$10</p></div>
    <div class="item"><h4><span>Shrimp &amp; Grits</span><span>$28</span></h4><p>Shrimp sautéed with onions, peppers, tomatoes in Cajun cream over cheesy grits.<br>Add crab meat +$10</p></div>
    <div class="item"><h4><span>Creole Herb Chicken</span><span>$28</span></h4><p>Roasted half chicken with creamy Creole sauce. Served with two sides.</p></div>
    <div class="item"><h4><span>Creole Salmon</span><span>$30</span></h4><p>Pan-seared salmon with creamy Creole sauce. Served with two sides. Add crab meat +$10</p></div>
    <div class="item"><h4><span>Bayou Pasta</span><span>$26</span></h4><p>Cream sauce with peppers, tomatoes, onions over linguine, topped with blackened chicken.</p></div>
    <div class="item"><h4><span>Pork Chops</span><span>$25</span></h4><p>Fried or grilled pork chops smothered in Southern gravy. Served with two sides.</p></div>
    <h2 class="heading" style="margin:3px 0 4px">Non-Alcoholic Specialties</h2>
    <div class="item item--tight"><h4><span>Blueberry Fizz</span><span>$12</span></h4><p>Blueberry, lime, ginger beer.</p></div>
    <div class="item item--tight"><h4><span>Pineapple Punch</span><span>$12</span></h4><p>Orange and pineapple juice, mai tai mix, peach, lime.</p></div>
  </div>

  <div class="divider" style="left:171px;top:84px;height:596px"></div>

  <div class="col" style="left:181px;top:88px;width:149px">
    <div class="item"><h4><span>Crab Cakes</span><span>market price</span></h4><p>Two broiled jumbo lump crab cakes served with two sides.</p></div>
    <div class="item"><h4><span>Red Snapper</span><span>market price</span></h4><p>Fried or roasted snapper with jambalaya stew and two sides.</p></div>
    <div class="item"><h4><span>Oxtails</span><span>$40</span></h4><p>Braised oxtails with butter beans. Served with two sides.</p></div>
    <div class="item"><h4><span>Catfish &amp; Grits</span><span>$28</span></h4><p>Blackened or fried catfish over white cheddar grits with Cajun cream sauce.<br>Add crab meat +$10</p></div>
    <div class="item"><h4><span>Caribbean Lamb Chops</span><span>$45</span></h4><p>Seasoned lamb chops with sweet Caribbean glaze. Served with two sides.</p></div>
    <h2 class="heading" style="margin:12px 0 11px">Sides</h2>
    <ul class="sides">
      <li><span>Cajun crab fries</span><span>$18</span></li>
      <li><span>Spinach</span><span>$7</span></li>
      <li><span>Lemon herb broccolini</span><span>$9</span></li>
      <li><span>Asparagus</span><span>$9</span></li>
      <li><span>Five-cheese mac</span><span>$9</span></li>
      <li><span>Fried rice</span><span>$8</span></li>
      <li><span>Seafood fried rice</span><span>$15</span></li>
      <li><span>Mashed potatoes</span><span>$8</span></li>
      <li><span>Seafood mac and cheese</span><span>$15</span></li>
      <li><span>Red beans and rice</span><span>$9</span></li>
      <li><span>Cheesy grits</span><span>$4</span></li>
      <li><span>Honey cornbread</span><span>$6</span></li>
      <li><span>Cajun fries</span><span>$4</span></li>
      <li><span>Sweet potato casserole</span><span>$7</span></li>
      <li><span>Collard greens with smoked turkey</span><span>$8</span></li>
    </ul>
    <h2 class="heading" style="margin:10px 0 4px">Beverages</h2>
    <div class="item item--tight"><h4><span>Soft drinks</span><span>$4</span></h4><p>Free refills<br>Cola • Diet Cola • Lemon-lime soda<br>Orange juice • Ginger ale<br>Pineapple juice • Cranberry juice</p></div>
    <div class="item item--tight" style="margin-top:3px"><h4><span>Creole lemonade &amp; sweet tea</span><span>$5</span></h4><p>Strawberry • Peach • Mango •<br>Watermelon • Kiwi • Blueberry</p></div>
    <div style="margin-top:5px">
      <p class="bev-row"><span>Ginger beer</span><span class="bev-price">$4</span></p>
      <p class="bev-row"><span>Vena Still</span><span class="bev-price">$5</span></p>
      <p class="bev-row"><span>Sorgente Sparkling</span><span class="bev-price">$5</span></p>
    </div>
  </div>

  <div class="divider" style="left:336px;top:84px;height:596px"></div>

  <div class="col" style="left:345px;top:48px;width:152px">
    <h2 class="heading" style="margin-bottom:12px;line-height:14px">Specialty<br>Cocktails</h2>
    <div class="item item--tight"><h4><span>Miss Delphine’s Hurricane</span><span>$16</span></h4><p>Dark rum, light rum, passionfruit, punch, lime, orange juice, grenadine.</p></div>
    <div class="item item--tight"><h4><span>Tsunami</span><span>$16</span></h4><p>Blanco tequila, pineapple, orange, passionfruit, blue curaçao, topped with dark tequila.</p></div>
    <div class="item item--tight"><h4><span>Secrets</span><span>$15</span></h4><p>Three-rum tropical blend with lime.</p></div>
    <div class="item item--tight"><h4><span>Smoked in Fashion</span><span>$18</span></h4><p>Bourbon, sugar cube, black cherry, orange and cherry bitters.</p></div>
    <div class="item item--tight"><h4><span>Smoked Tequila Old Fashion</span><span>$18</span></h4><p>Aged tequila, orange liqueur, agave, peach bitters, orange peel.</p></div>
    <div class="item item--tight"><h4><span>Miskiri</span><span>$17</span></h4><p>Tequila, Gran Solera, blackberry, pineapple, cranberry, lemon.</p></div>
    <div class="item item--tight"><h4><span>Blackberry French</span><span>$15</span></h4><p>Azalea 1912 gin, lemonade, champagne, blackberry, white flower.</p></div>
    <div class="item item--tight"><h4><span>Margarita or Lemon Drop Flight</span><span>$20</span></h4><p>Traditional • Strawberry • Blueberry • Passionfruit (on the rocks)</p></div>
    <div class="item item--tight"><h4><span>Louisiana Tea</span><span>$17</span></h4><p>Old Marrow whiskey, honey mint syrup, lemonade.</p></div>
    <div class="item item--tight"><h4><span>Pink Lady</span><span>$15</span></h4><p>Tequila, orange liqueur, lime, strawberry-kiwi, agave.</p></div>
    <div class="item item--tight"><h4><span>Creole Island</span><span>$19</span></h4><p>Gran Solera, Harcourt cognac, tropical punch.</p></div>
    <div class="item item--tight"><h4><span>Becky Sangria</span><span>$18</span></h4><p>Red wine blend, Harcourt cognac, fruit punch, frozen popsicle.</p></div>
    <div class="item item--tight"><h4><span>Pineapple-gria</span><span>$18</span></h4><p>White sparkling wine, rum, pineapple punch.</p></div>
    <div class="item item--tight"><h4><span>Peach Please</span><span>$16</span></h4><p>Vodka, peach nectar, champagne.</p></div>
    <div class="item item--tight"><h4><span>Toasted Marshmallow Espresso Martini</span><span>$16</span></h4><p>Toasted marshmallow, espresso, vodka, cream, white chocolate liqueur.</p></div>
    <div class="item item--tight"><h4><span>Delphine’s Passion</span><span>$18</span></h4><p>Delacroix VSOP, orange liqueur, lemon, passionfruit.</p></div>
  </div>
</section>

</body>
</html>
```